Automotive eCommerce Business looking for a business card design

Looking for a clean and simple business card design. Our company name is "Brindle Auto" and we are a company specializing in the ecommerce sales of automotive parts, specifically for pick up trucks and large SUVs. Our company colours are red, black, and white.

Feel free to use the logo provided or create a new logo that you seem fit. Looking forward to your creative ideas!

Industry/Entity Type

Automotive

Contact Information for Business Card

We were thinking of a possibly two-sided design featuring just the logo and company name on one side, and personal information on the other side. Single sided designs will be considered as well.

Font styles to use
Serif
Sans Serif
Decorative

Colors
ec1f27
ffffff
000000

Requirements
Must have
• Space for employee's name, title, phone number and email address, along with the company address and website somewhere.

```html
<!DOCTYPE html>
<html lang="en">
<head>
<meta charset="utf-8">
<title>Brindle Auto Ltd. — Business Card</title>
<link rel="stylesheet" href="https://fonts.googleapis.com/css2?family=Cinzel:wght@400&family=Roboto:wght@400;500&display=swap">
<style>
  :root {
    --backdrop: #e8e6e3;
    --card: #f6f6f5;
    --brand-red: #a31c22;
    --wordmark: #535353;
    --url-grey: #555555;
    --on-red: #ffffff;
  }
  * { box-sizing: border-box; margin: 0; padding: 0; }
  html, body {
    width: 1200px;
    height: 960px;
    overflow: hidden;
    background: var(--backdrop);
  }
  .canvas {
    position: relative;
    width: 1200px;
    height: 960px;
  }
  .card {
    position: absolute;
    left: 300px;
    width: 600px;
    height: 342px;
    background: var(--card);
    border-radius: 20px;
    overflow: hidden;
    box-shadow: 0 2px 6px rgba(0,0,0,0.18);
  }
  .card--front { top: 95px; }
  .card--back { top: 500px; }

  .brand-mark {
    position: absolute;
    left: 50%;
    top: 78px;
    width: 150px;
    height: 150px;
    margin-left: -75px;
    border-radius: 50%;
    background: var(--brand-red);
  }
  .wordmark {
    position: absolute;
    left: 0;
    right: 0;
    text-align: center;
    font-family: "Cinzel", serif;
    font-weight: 400;
    font-size: 28px;
    color: var(--wordmark);
    letter-spacing: 0.5px;
  }
  .card--front .wordmark { top: 242px; }
  .card--back .wordmark { top: 42px; }

  .website {
    position: absolute;
    left: 0;
    right: 0;
    top: 303px;
    text-align: center;
    font-family: "Roboto", sans-serif;
    font-size: 14px;
    letter-spacing: 5px;
    color: var(--url-grey);
  }

  .contact-band {
    position: absolute;
    left: 0;
    top: 0;
    width: 600px;
    height: 342px;
  }
  .contact-band path { fill: var(--brand-red); }

  .contact {
    position: absolute;
    left: 0;
    right: 0;
    top: 158px;
    text-align: center;
    font-family: "Roboto", sans-serif;
    color: var(--on-red);
  }
  .contact__name {
    font-size: 20px;
    font-weight: 500;
    line-height: 24px;
  }
  .contact__title {
    font-size: 15px;
    line-height: 22px;
    margin-bottom: 26px;
  }
  .contact__line {
    font-size: 14px;
    line-height: 19px;
  }
  .contact__address {
    font-size: 14px;
    line-height: 19px;
    margin-top: 5px;
  }
</style>
</head>
<body>
<main class="canvas">
  <section class="card card--front" aria-label="Card front">
    <div class="brand-mark"></div>
    <h1 class="wordmark">Brindle Auto Ltd.</h1>
    <p class="website">www.brindleauto.com</p>
  </section>

  <section class="card card--back" aria-label="Card back">
    <h2 class="wordmark">Brindle Auto Ltd.</h2>
    <svg class="contact-band" viewBox="0 0 600 342" aria-hidden="true">
      <path d="M0 272 C 90 205, 200 115, 300 115 C 410 115, 470 165, 540 208 C 575 230, 592 248, 600 262 L 600 342 L 0 342 Z"/>
    </svg>
    <div class="contact">
      <p class="contact__name">MARA QUINLAN</p>
      <p class="contact__title">CEO/FOUNDER</p>
      <p class="contact__line">P: 555 014 2290</p>
      <p class="contact__line">C: 555 017 6612 F: 555 019 4403</p>
      <p class="contact__line">E: mara@brindleauto.com W: www.brindleauto.com</p>
      <p class="contact__address">412 Harrow Field Road, Millbrook, Ohio 40218</p>
    </div>
  </section>
</main>
</body>
</html>
```